Business cards for KORU Real Estate Holdings LLC

We need a cool, original business card design for a company based in the Washington DC metropolitan area. We are a new energetic and passionate Real Estate Investing Company that invests in all types of real estate; commercial, residential, industrial etc.

Our company color is Red since it reflects action, energy and speed; it is assertive confident, energizing, exciting, powerful, passionate and determined. So we would like business card communicate those qualities to the audience.

Our audiences are investors that want to invest with us, real estate sellers, buyers, and tenants who lease from us.

Our logo is attached

```html
<!DOCTYPE html>
<html lang="en">
<head>
<meta charset="utf-8">
<title>KORU Real Estate Holdings LLC — Business Cards</title>
<link href="https://fonts.googleapis.com/css2?family=Roboto+Condensed:wght@400;700&family=Roboto:wght@400&display=swap" rel="stylesheet">
<style>
  :root {
    --backdrop: #ebe6dc;
    --card-dark: #1b1b1c;
    --card-mid: #2e2f31;
    --card-sheen: #3c3d40;
    --panel-dark: #141415;
    --brand-red: #a3141a;
    --brand-red-deep: #7a0c10;
    --text-white: #f2f2f2;
    --text-grey: #c9c9c9;
  }
  * { margin: 0; padding: 0; box-sizing: border-box; }
  html, body {
    width: 1200px; height: 960px; overflow: hidden;
    background: var(--backdrop);
  }
  .sheet { position: relative; width: 1200px; height: 960px; }

  .card {
    position: absolute;
    width: 640px; height: 360px;
    overflow: hidden;
    background:
      repeating-linear-gradient(90deg, rgba(255,255,255,0.018) 0 1px, transparent 1px 3px),
      linear-gradient(115deg, var(--card-dark) 0%, var(--card-mid) 38%, var(--card-sheen) 50%, var(--card-mid) 62%, var(--card-dark) 100%);
    box-shadow: 0 6px 14px rgba(0,0,0,0.35);
  }

  /* Info side */
  .card--info { left: 110px; top: 90px; }
  .card--info .brand-panel {
    position: absolute; left: 0; top: 0; width: 178px; height: 100%;
    background: linear-gradient(180deg, var(--panel-dark), #232325 55%, var(--panel-dark));
  }
  .card--info .red-band {
    position: absolute; left: 178px; top: 0; width: 20px; height: 100%;
    background: linear-gradient(90deg, var(--brand-red-deep), var(--brand-red), var(--brand-red-deep));
  }
  .brand-vertical {
    position: absolute; left: 89px; top: 180px;
    width: 320px;
    transform: translate(-50%, -50%) rotate(-90deg);
    display: flex; flex-direction: column; align-items: center;
    font-family: "Roboto Condensed", sans-serif; color: var(--text-white);
  }
  .brand-vertical .brand-row { display: flex; align-items: center; gap: 14px; }
  .brand-mark-dot {
    width: 30px; height: 30px; border-radius: 50%; background: var(--brand-red);
  }
  .brand-vertical .brand-name {
    font-weight: 700; font-size: 64px; letter-spacing: 4px; line-height: 1;
  }
  .brand-vertical .brand-sub {
    font-weight: 400; font-size: 17px; letter-spacing: 0.5px; margin-top: 4px;
  }

  .person {
    position: absolute; left: 232px; top: 158px;
    font-family: "Roboto Condensed", sans-serif; text-transform: uppercase;
  }
  .person .person-name { font-size: 18px; color: var(--brand-red); letter-spacing: 0.5px; }
  .person .person-name span { color: var(--text-white); }
  .person .person-role { font-size: 12px; color: var(--brand-red); letter-spacing: 1px; margin-left: 52px; }

  .contact-list {
    position: absolute; left: 410px; top: 128px; list-style: none;
    font-family: "Roboto", sans-serif; font-size: 13px; color: var(--text-white);
  }
  .contact-list li { display: flex; align-items: center; gap: 10px; height: 22px; }
  .contact-list svg { width: 14px; height: 14px; fill: var(--text-white); flex: none; }

  /* Logo side */
  .card--logo { left: 400px; top: 500px; }
  .brand-center {
    position: absolute; left: 50%; top: 50%;
    transform: translate(-50%, -50%);
    display: flex; flex-direction: column; align-items: center;
    font-family: "Roboto Condensed", sans-serif; color: var(--text-white);
  }
  .brand-center .brand-row { display: flex; align-items: center; gap: 22px; }
  .brand-center .brand-mark-dot { width: 52px; height: 52px; }
  .brand-center .brand-name {
    font-weight: 700; font-size: 96px; letter-spacing: 6px; line-height: 1;
  }
  .brand-center .brand-sub {
    font-weight: 400; font-size: 24px; letter-spacing: 0.5px; margin-top: 8px;
  }
</style>
</head>
<body>
<main class="sheet">

  <section class="card card--info" aria-label="Business card, contact side">
    <div class="brand-panel"></div>
    <div class="red-band"></div>

    <div class="brand-vertical">
      <div class="brand-row">
        <span class="brand-mark-dot"></span>
        <span class="brand-name">KORU</span>
      </div>
      <span class="brand-sub">REAL ESTATE HOLDINGS LLC</span>
    </div>

    <div class="person">
      <p class="person-name">Name <span>Surname</span></p>
      <p class="person-role">Manager</p>
    </div>

    <ul class="contact-list">
      <li>
        <svg viewBox="0 0 14 14" aria-hidden="true"><rect x="3.5" y="0.5" width="7" height="13" rx="1.5"/></svg>
        55 5555 5555
      </li>
      <li>
        <svg viewBox="0 0 14 14" aria-hidden="true"><path d="M1 5c0-2 2.5-3 6-3s6 1 6 3v1h-3V4.5H4V6H1z"/><rect x="2.5" y="7" width="9" height="5.5" rx="1"/></svg>
        44 4444 4444
      </li>
      <li>
        <svg viewBox="0 0 14 14" aria-hidden="true"><path d="M1 3h12v8H1z M1.8 3.8 7 8l5.2-4.2" fill="none" stroke="#f2f2f2" stroke-width="1.1"/></svg>
        info@korurealestate.com
      </li>
      <li>
        <svg viewBox="0 0 14 14" aria-hidden="true"><g fill="none" stroke="#f2f2f2" stroke-width="1"><circle cx="7" cy="7" r="6"/><ellipse cx="7" cy="7" rx="2.6" ry="6"/><path d="M1 7h12M2 4h10M2 10h10"/></g></svg>
        www.korurealestate.com
      </li>
      <li>
        <svg viewBox="0 0 14 14" aria-hidden="true"><path d="M7 0.5a4.5 4.5 0 0 1 4.5 4.5C11.5 8.5 7 13.5 7 13.5S2.5 8.5 2.5 5A4.5 4.5 0 0 1 7 0.5z"/></svg>
        area,state,zipcode,country
      </li>
    </ul>
  </section>

  <section class="card card--logo" aria-label="Business card, brand side">
    <div class="brand-center">
      <div class="brand-row">
        <span class="brand-mark-dot"></span>
        <span class="brand-name">KORU</span>
      </div>
      <span class="brand-sub">REAL ESTATE HOLDINGS LLC</span>
    </div>
  </section>

</main>
</body>
</html>
```